Modern Business Card

Modern professional business card with more than just logo and demographic info. Something memorable.

We are a trendy/modern chiropractic group with an emphasis on neurology, hence the minimalist-type brain logo. We want to convey that modern and technical aspect with professionalism and the elite nature of our practice environment.

```html
<!DOCTYPE html>
<html lang="en">
<head>
<meta charset="utf-8">
<title>Meridian Spine – Business Card</title>
<link rel="stylesheet" href="https://fonts.googleapis.com/css2?family=Crimson+Text:wght@400;600&family=Fira+Sans:wght@600&display=swap">
<style>
  :root {
    --backdrop: #3b3b3d;
    --card-black: #1c1c1e;
    --band-blue: #4a6aaa;
    --ink-white: #f4f4f4;
    --front-mark: #8a8a8e;
    --band-mark: #1c1c1e;
  }
  * { margin: 0; padding: 0; box-sizing: border-box; }
  html, body { width: 799px; height: 1200px; overflow: hidden; }
  body {
    background: var(--backdrop);
    font-family: "Crimson Text", Georgia, serif;
    color: var(--ink-white);
    display: flex;
    flex-direction: column;
    align-items: center;
    justify-content: space-evenly;
  }
  .card {
    position: relative;
    width: 640px;
    height: 366px;
    background: var(--card-black);
    border-radius: 6px;
    overflow: hidden;
    box-shadow: 0 14px 30px rgba(0,0,0,.45);
  }

  /* Front */
  .card--front { display: flex; align-items: center; justify-content: center; }
  .front-wordmark {
    font-size: 46px;
    font-weight: 600;
    letter-spacing: 4px;
    text-transform: uppercase;
    color: var(--front-mark);
  }

  /* Back */
  .brand-row {
    position: absolute;
    top: 22px; left: 30px;
    display: flex; align-items: center; gap: 12px;
  }
  .brand-square { width: 26px; height: 26px; background: var(--band-blue); }
  .brand-name {
    font-size: 30px;
    font-weight: 400;
    letter-spacing: 1px;
    text-transform: uppercase;
    color: var(--ink-white);
  }
  .contact-band {
    position: absolute;
    top: 84px; left: 0; right: 0;
    height: 196px;
    background: var(--band-blue);
  }
  .person { position: absolute; top: 20px; left: 52px; }
  .person-name {
    font-family: "Fira Sans", Arial, sans-serif;
    font-weight: 600;
    font-size: 21px;
    line-height: 1.1;
  }
  .person-title { font-size: 16px; line-height: 1.2; }
  .contact-list {
    position: absolute;
    top: 96px; left: 30px;
    list-style: none;
    font-size: 16px;
    line-height: 22px;
  }
  .contact-list li { display: flex; align-items: center; gap: 10px; }
  .contact-list svg { width: 13px; height: 13px; fill: var(--ink-white); }
  .band-wordmark {
    position: absolute;
    right: 28px; top: 50%;
    transform: translateY(-50%);
    font-size: 44px;
    font-weight: 600;
    letter-spacing: 3px;
    text-transform: uppercase;
    color: var(--band-mark);
  }
  .address {
    position: absolute;
    left: 30px; bottom: 40px;
    font-size: 16px;
  }
</style>
</head>
<body>

  <section class="card card--front" aria-label="Card front">
    <span class="front-wordmark">Meridian Spine</span>
  </section>

  <section class="card card--back" aria-label="Card back">
    <div class="brand-row">
      <span class="brand-square"></span>
      <span class="brand-name">Meridian Spine</span>
    </div>

    <div class="contact-band">
      <div class="person">
        <p class="person-name">Evan Cole Harper</p>
        <p class="person-title">Managing Director</p>
      </div>
      <ul class="contact-list">
        <li>
          <svg viewBox="0 0 16 16" aria-hidden="true"><path d="M3 1h3l1.5 4-2 1.3a9 9 0 0 0 4.2 4.2L11 8.5l4 1.5v3a2 2 0 0 1-2 2A12 12 0 0 1 1 3a2 2 0 0 1 2-2z"/></svg>
          555-014-2270
        </li>
        <li>
          <svg viewBox="0 0 16 16" aria-hidden="true"><path d="M1 3h14v10H1z M1 3l7 6 7-6" fill="none" stroke="#f4f4f4" stroke-width="1.6"/></svg>
          evan@meridianspine.com
        </li>
        <li>
          <svg viewBox="0 0 16 16" aria-hidden="true"><circle cx="8" cy="8" r="6.5" fill="none" stroke="#f4f4f4" stroke-width="1.4"/><path d="M1.5 8h13M8 1.5c-3 3.5-3 9.5 0 13M8 1.5c3 3.5 3 9.5 0 13" fill="none" stroke="#f4f4f4" stroke-width="1.2"/></svg>
          www.meridianspine.com
        </li>
      </ul>
      <span class="band-wordmark">Meridian Spine</span>
    </div>

    <p class="address">87 Lantern Row, Brookfield, US 40521</p>
  </section>

</body>
</html>
```